Brand New Product Needs Sales Focused Website Design

Looking for design of Homepage, Category Page & Product Page for single product sales focused website. TrundleCrate manufacture and distribute a brand new product to the market called PalTote-Case which is a super strong, re-useable, folding & stacking plastic box which can be seen on our current website www.paltote-case.example PalTote-Case was originally developed as an alternative to supermarket carrier bags and was pitched as a box for life against the other low end re-useable products. The original version was made from recycled plastic and pitched very much as environmental product. We are now taking a different direction and have re-designed the boxes in 5 bright and fashionable designs and although we still want the primary focus to be supermarket shopping we want to position the product as a design led, must have shopping and household accessory rather than a boring, cheap looking black plastic box. The new designs will still have the environmental benefits of being able to be re-used thousands of times and being 100% recyclable and save on the imminent 5p tax on carrier bags in the UK however the new designs will not be made from recycled material. Although the main use for PalTote-Case is supermarket shopping it has a multitude of other uses especially where you need temporary storage - laundry, back of the car, moving house/students, gardening, days out, home office filing (will take A4 file), recycling and much more - PalTote-Case is made out of super strong Polypropylene and can be easily washed and sanitised after use and can be folded and unfolded thousands of times and so will last for many years. PalTote-Case is a product that needs to be seen in action to be understood so the web design must quickly and easily communicate what PalTote-Case is and how it works - this can be done with video, images and copy. Our current website does not work for many reasons:- it is too busy, has too much information, tries too hard and ultimately isn't working. Any of the images off our current website can be supplied for use. Once the concept of the website is agreed I can get these photoshopped with the new designs. Pictures of new designs for reference will be attached to this brief. Ultimately we want the website to convert visitors to sales and therefore designers with a proven track record in this field are especially welcome to enter. We also have a Dropbox folder with over 100 product and situation images in - please send email address and we will send an invite to the folder. Due to Christmas period this competition will be run over 15 days however we may choose to extend the deadline to account for the non working days. Any questions feel free to ask - we will respond within 24 hours where possible.

```html
<!DOCTYPE html>
<html lang="en">
<head>
<meta charset="utf-8">
<title>PalTote-Case – Ingenious &amp; Practical</title>
<link rel="stylesheet" href="https://fonts.googleapis.com/css2?family=Montserrat:wght@400;500;600;700&family=Pacifico&family=Lato:wght@400;700&display=swap">
<style>
:root{
  --pink:#dc4f96;
  --pink-dark:#c63f84;
  --ink:#222222;
  --nav:#232323;
  --text:#333333;
  --muted:#6b6b6b;
  --panel:#f1f1f1;
  --grey:#e2e2e2;
  --footer:#3c3c3c;
  --footer-bar:#222222;
  --footer-text:#bdbdbd;
  --white:#ffffff;
}
*{margin:0;padding:0;box-sizing:border-box}
html,body{width:1200px;height:2517px;overflow:hidden;background:var(--white)}
body{position:relative;font-family:'Montserrat',sans-serif;color:var(--text)}
.abs{position:absolute}

/* header */
.brand{left:111px;top:34px;font-family:'Montserrat',sans-serif;font-weight:700;font-size:52px;color:var(--pink);letter-spacing:-1px;line-height:1}
.tagline{left:144px;top:110px;font-size:19px;font-weight:500;color:var(--ink);letter-spacing:.5px}
.search{left:693px;top:27px;width:255px;height:35px;border:1px solid #cfcfcf;display:flex}
.search span{flex:1;font-size:13px;color:#999;padding:9px 10px;font-family:'Lato',sans-serif}
.search b{width:38px;background:var(--pink);display:flex;align-items:center;justify-content:center}
.currency{left:978px;top:27px;width:113px;height:35px;border:1px solid #cfcfcf;display:flex;font-size:12px}
.currency span{flex:1;display:flex;align-items:center;justify-content:center;color:var(--ink);font-weight:600;border-right:1px solid #cfcfcf}
.currency em{width:44px;display:flex;align-items:center;justify-content:center;color:var(--pink);font-style:normal}
.cart{left:910px;top:96px;display:flex;align-items:center;gap:12px;font-size:26px;color:var(--ink)}

/* nav */
.nav{left:0;top:159px;width:1200px;height:49px;background:var(--nav)}
.nav ul{position:absolute;left:111px;top:0;display:flex;list-style:none;height:49px}
.nav li{height:49px;display:flex;align-items:center;justify-content:center;color:var(--white);font-size:14px;border-right:1px solid #3a3a3a}
.nav li.active{background:var(--pink)}

/* hero */
.hero{left:0;top:208px;width:1200px;height:542px;background:linear-gradient(90deg,#3a2a22 0%,#5b4638 30%,#7b5a3e 55%,#c79a4a 75%,#8e6c3a 100%)}
.hero-photo{left:420px;top:208px;width:780px;height:542px;background:radial-gradient(ellipse at 55% 60%,#e8572a 0%,#e0a84a 30%,rgba(245,200,40,.6) 55%,rgba(120,90,60,0) 80%)}
.hero-title{left:111px;top:290px;font-family:'Pacifico',cursive;color:var(--white);font-size:54px;line-height:1.25}
.hero-sub{left:111px;top:452px;color:var(--white);font-size:14px;font-weight:500}
.hero-copy{left:111px;top:482px;width:320px;color:var(--white);font-size:13px;line-height:23px;font-family:'Lato',sans-serif}
.btn{display:flex;align-items:center;justify-content:center;color:var(--white);font-size:13px;font-weight:500;background:var(--pink)}
.btn-ghost{background:transparent;border:1px solid var(--white)}

/* box for life */
.life-card{left:111px;top:814px;width:501px;height:310px;background:var(--panel)}
.life-title{left:136px;top:836px;font-size:38px;color:var(--ink);font-weight:400}
.life-copy{left:136px;top:904px;width:210px;font-size:13.5px;line-height:24px;color:var(--ink);font-weight:500}
.life-photo{left:352px;top:820px;width:258px;height:304px;background:linear-gradient(160deg,#e8e8e8 0%,#2c4aa0 55%,#1f2a55 100%)}
.video{left:659px;top:814px;width:432px;height:310px;background:linear-gradient(180deg,#f3f3f3 0%,#cfcfcf 45%,#5a5a5a 100%)}
.video-play{left:838px;top:928px;width:73px;height:46px;background:#2b2b2b;border-radius:4px;display:flex;align-items:center;justify-content:center}
.video-bar{left:659px;top:1082px;width:432px;height:42px;background:#121212}

/* designs band */
.designs{left:0;top:1210px;width:1200px;height:455px;background:linear-gradient(90deg,#f2f2f2 0%,#e9e9ea 45%,#d8dcdc 75%,#cfd6d4 100%)}
.designs-photo{left:663px;top:1210px;width:369px;height:455px;background:linear-gradient(180deg,#3fae7a 0%,#3fae7a 14%,#f6f4f0 32%,#f1e7ee 70%,#a6c64a 92%,#a6c64a 100%)}
.designs-title{left:103px;top:1256px;font-size:33px;line-height:49px;color:var(--ink);font-weight:400}
.designs-title b{font-size:40px;font-weight:600}
.designs-copy{left:104px;top:1378px;width:470px;font-size:13.5px;line-height:25px;color:#555;font-family:'Lato',sans-serif}

/* new products */
.np-title{left:111px;top:1718px;font-size:37px;color:var(--ink)}
.np-rule{left:383px;top:1744px;width:607px;height:3px;border-top:1px solid #dcdcdc;border-bottom:1px solid #dcdcdc}
.arrow{top:1730px;width:30px;height:28px;border:1px solid #d6d6d6;display:flex;align-items:center;justify-content:center}
.product{top:1826px;width:228px;height:271px}
.product-tab{position:absolute;left:57px;top:0;width:114px;height:50px;border-radius:57px 57px 0 0;background:var(--grey)}
.product-head{position:absolute;left:0;top:27px;width:228px;height:33px;background:var(--grey)}
.product-name{position:absolute;left:0;top:6px;width:228px;text-align:center;font-family:Georgia,serif;font-size:20px;line-height:22px;color:#444}
.product-img{position:absolute;left:0;top:60px;width:228px;height:168px;border:1px solid #dedede;border-bottom:0;background:var(--white)}
.product-box{position:absolute;left:26px;top:42px;width:176px;height:90px;background:linear-gradient(180deg,#f4f4f4 0%,#ececec 55%,#b4cc4c 100%);border-radius:4px}
.product-foot{position:absolute;left:0;top:228px;width:228px;height:43px;display:flex}
.price{width:105px;background:var(--grey);color:var(--pink);font-size:15px;display:flex;align-items:center;justify-content:center}
.shop{flex:1;background:var(--pink);color:var(--white);font-size:13px;font-weight:500;display:flex;align-items:center;justify-content:center}
.product.active .product-tab,.product.active .product-head{background:var(--pink)}
.product.active .product-name{color:var(--white)}
.product.active .product-img{border-color:var(--pink)}
.product.active .price{background:var(--white);border:1px solid var(--pink);border-right:0}
.box-alt{background:linear-gradient(180deg,#f6f6f6 0%,#eeeeee 50%,#e7d0c8 62%,#c2784d 70%,#f3f3f3 78%)}

/* footer */
.footer{left:0;top:2203px;width:1200px;height:267px;background:var(--footer)}
.f-head{top:2246px;font-size:19px;color:var(--white);font-weight:400}
.f-about{left:111px;top:2284px;width:230px;font-size:10.5px;line-height:13px;color:var(--footer-text);font-family:'Lato',sans-serif}
.f-contact{left:111px;top:2378px;font-size:12px;color:var(--footer-text);line-height:27px;font-family:'Lato',sans-serif}
.f-contact b{display:inline-block;width:60px;font-weight:400}
.f-contact .val{color:var(--white)}
.f-contact .mail{color:var(--pink)}
.f-list{top:2296px;list-style:none;font-size:11px;line-height:18px;color:var(--footer-text);font-family:'Lato',sans-serif}
.f-news{left:839px;top:2279px;width:220px;font-size:10.5px;line-height:12px;color:var(--footer-text);font-family:'Lato',sans-serif}
.f-input{left:839px;top:2322px;width:180px;height:28px;background:var(--white);font-size:10px;color:#888;padding:8px 12px}
.f-submit{left:1019px;top:2322px;width:70px;height:28px;font-size:11px}
.pay{top:2394px;width:38px;height:23px;border-radius:3px;background:#e8e8e8}
.bottom{left:0;top:2470px;width:1200px;height:47px;background:var(--footer-bar);color:var(--white);font-size:13px}
.bottom .copy{position:absolute;left:111px;top:15px}
.bottom .links{position:absolute;right:111px;top:15px}
</style>
</head>
<body>

<header>
  <div class="abs brand">PalTote-Case</div>
  <div class="abs tagline">INGENIOUS &amp; PRACTICAL</div>
  <div class="abs search"><span>Search...</span><b><svg width="16" height="16" viewBox="0 0 16 16"><circle cx="6.5" cy="6.5" r="4.5" fill="none" stroke="#fff" stroke-width="2"/><line x1="10" y1="10" x2="14" y2="14" stroke="#fff" stroke-width="2.4" stroke-linecap="round"/></svg></b></div>
  <div class="abs currency"><span>Currency</span><em>USD</em></div>
  <div class="abs cart">
    <svg width="34" height="30" viewBox="0 0 34 30"><path d="M2 4h6l4 16h16l4-12H10" fill="none" stroke="#dc4f96" stroke-width="2.4" stroke-linejoin="round"/><line x1="13" y1="12" x2="29" y2="12" stroke="#dc4f96" stroke-width="2"/><circle cx="14" cy="25" r="2.5" fill="#dc4f96"/><circle cx="26" cy="25" r="2.5" fill="#dc4f96"/></svg>
    <span>My Cart : 0</span>
  </div>
</header>

<nav class="abs nav">
  <ul>
    <li class="active" style="width:114px">HOME</li>
    <li style="width:170px">CATAGORY</li>
    <li style="width:175px">OUR RANGE</li>
    <li style="width:170px">GAURANTEE</li>
    <li style="width:160px">PRODUCTS</li>
    <li style="width:191px;border-right:1px solid #3a3a3a">CONTACT US</li>
  </ul>
</nav>

<section>
  <div class="abs hero" role="img" aria-label="Blurred supermarket aisle backdrop"></div>
  <div class="abs hero-photo" role="img" aria-label="Smiling shopper beside an orange crate filled with groceries"></div>
  <h1 class="abs hero-title">Welcome To<br>PalTote-Case</h1>
  <p class="abs hero-sub">INGENIOUS &amp; PRACTICAL BOX FOR LIFE</p>
  <p class="abs hero-copy">Lorem ipsum dolor sit amet, consectetur adipiscing elit. In quis enim est. Quisque lobortis commodo</p>
  <a class="abs btn" style="left:111px;top:559px;width:141px;height:40px">LEARN MORE</a>
  <a class="abs btn btn-ghost" style="left:280px;top:559px;width:145px;height:40px">SHOP NOW</a>
</section>

<section>
  <div class="abs life-card"></div>
  <div class="abs life-photo" role="img" aria-label="Woman carrying a folding crate full of fresh produce"></div>
  <h2 class="abs life-title">BOX FOR LIFE</h2>
  <p class="abs life-copy">Lorem ipsum dolor sit amet, consectetur adipiscing elit. Pellentesque est diam, consequat at viverra vel, sagittis et risus. Nulla facilisi. Integer augue leo,</p>
  <a class="abs btn" style="left:136px;top:1057px;width:132px;height:40px">VIEW EXAMPLES</a>

  <div class="abs video" role="img" aria-label="Product video still: presenter demonstrating the folding box beside a shopping trolley"></div>
  <div class="abs video-play"><svg width="20" height="22" viewBox="0 0 20 22"><path d="M2 1l17 10L2 21z" fill="#fff"/></svg></div>
  <div class="abs video-bar">
    <svg width="432" height="42" viewBox="0 0 432 42">
      <rect x="0" y="0" width="432" height="3" fill="#555"/><rect x="0" y="0" width="300" height="3" fill="#d21f2a"/>
      <rect x="16" y="16" width="3" height="10" fill="#fff"/><rect x="22" y="16" width="3" height="10" fill="#fff"/>
      <path d="M285 17h4l5-4v16l-5-4h-4z" fill="#fff"/>
      <rect x="305" y="20" width="45" height="3" fill="#d21f2a"/>
      <path d="M397 14h6M397 14v6M413 28h-6M413 28v-6" stroke="#fff" stroke-width="2" fill="none"/>
    </svg>
  </div>
</section>

<section>
  <div class="abs designs" role="img" aria-label="Soft blurred shop shelf background"></div>
  <div class="abs designs-photo" role="img" aria-label="Hands holding a white box printed with bright flowers"></div>
  <h2 class="abs designs-title">NOW Available In <b>5</b> BRIGHT<br>&amp; FASHIONABLE designs</h2>
  <p class="abs designs-copy">Lorem ipsum dolor sit amet, consectetur adipiscing elit. Pellentesque est diam, consequat at viverra vel, sagittis et risus. Nulla facilisi. Integer augue leo, varius at odio a, dictum vehicula lacus. Nullam blandit, eros sed mollis mattis, est ipsum semper orci, ut malesuada eros elit vel mi. Nullam lacinia, ante sed feugiat elementum, nibh augue aliquet ante,</p>
  <a class="abs btn" style="left:106px;top:1550px;width:131px;height:41px">SHOP NOW</a>
</section>

<section>
  <h2 class="abs np-title">New Products</h2>
  <div class="abs np-rule"></div>
  <div class="abs arrow" style="left:1007px"><svg width="8" height="12" viewBox="0 0 8 12"><path d="M6 1L1 6l5 5" stroke="#999" fill="none"/></svg></div>
  <div class="abs arrow" style="left:1058px"><svg width="8" height="12" viewBox="0 0 8 12"><path d="M2 1l5 5-5 5" stroke="#999" fill="none"/></svg></div>

  <article class="abs product" style="left:109px">
    <div class="product-tab"></div><div class="product-head"></div>
    <div class="product-name">PalTote<br>Case</div>
    <div class="product-img"><div class="product-box" role="img" aria-label="Floral print folding box"></div></div>
    <div class="product-foot"><span class="price">$ 54.00</span><span class="shop">SHOP NOW</span></div>
  </article>
  <article class="abs product" style="left:359px">
    <div class="product-tab"></div><div class="product-head"></div>
    <div class="product-name">PalTote<br>Case</div>
    <div class="product-img"><div class="product-box box-alt" role="img" aria-label="White folding box with a patterned band"></div></div>
    <div class="product-foot"><span class="price">$ 54.00</span><span class="shop">SHOP NOW</span></div>
  </article>
  <article class="abs product active" style="left:609px">
    <div class="product-tab"></div><div class="product-head"></div>
    <div class="product-name">PalTote<br>Case</div>
    <div class="product-img"><div class="product-box" role="img" aria-label="Floral print folding box"></div></div>
    <div class="product-foot"><span class="price">$ 54.00</span><span class="shop">SHOP NOW</span></div>
  </article>
  <article class="abs product" style="left:859px">
    <div class="product-tab"></div><div class="product-head"></div>
    <div class="product-name">PalTote<br>Case</div>
    <div class="product-img"><div class="product-box box-alt" role="img" aria-label="White folding box with a patterned band"></div></div>
    <div class="product-foot"><span class="price">$ 54.00</span><span class="shop">SHOP NOW</span></div>
  </article>
</section>

<footer>
  <div class="abs footer"></div>
  <h3 class="abs f-head" style="left:111px;top:2250px">About Us</h3>
  <p class="abs f-about">Lorem ipsum dolor sit amet, consectetuer adipiscing elit. Aenean commodo ligula eget dolor. Aenean massa. Cum sociis natoque penatibus et magnis dis parturient montes, nascetur ridiculus mus. Donec quam felis, ultricies nec, pellentesque eu, pretium quis, sem.</p>
  <div class="abs f-contact">
    <div><b>Phone:</b><span class="val">1-555-010-2030</span></div>
    <div><b>e-mail:</b><span class="mail">info@northbay-trade.example</span></div>
  </div>

  <h3 class="abs f-head" style="left:435px">Lorem Ipsum</h3>
  <ul class="abs f-list" style="left:435px;top:2296px">
    <li>Lorem ipsum</li><li>Dolor sit</li><li>Amet</li><li>Consectutuer</li><li>Adipiscing</li>
  </ul>

  <h3 class="abs f-head" style="left:651px">Our Support</h3>
  <ul class="abs f-list" style="left:657px;top:2296px">
    <li>Site Map</li><li>Search Terms</li><li>Advanced Search</li><li>Mobile</li><li>Contact Us</li><li>Mobile</li><li>Addresses</li>
  </ul>

  <h3 class="abs f-head" style="left:839px">Newsletter</h3>
  <p class="abs f-news">Join thousands of other people subscribe to our news</p>
  <div class="abs f-input">INSERT EMAIL</div>
  <a class="abs btn f-submit">SUBMIT</a>

  <div class="abs pay" style="left:829px;background:#7fa9d9"></div>
  <div class="abs pay" style="left:876px;background:#e9a24a"></div>
  <div class="abs pay" style="left:922px;background:#5b7fc2"></div>
  <div class="abs pay" style="left:969px;background:#6fa0d8"></div>
  <div class="abs pay" style="left:1015px;background:#f0f0f0"></div>
  <div class="abs pay" style="left:1061px;background:#f4f4f4"></div>

  <div class="abs bottom">
    <span class="copy">© 2014 PalTote-Case All Rights Reserved</span>
    <span class="links">Privacy Policy &nbsp;|&nbsp; Terms &amp; Conditions</span>
  </div>
</footer>

</body>
</html>
```